Business Card Design for BrightvaleMedia.com

--I need a business card design for my company BrightvaleMedia.com

I have attached my logo...I want the brightvale media logo on the front of the business card, and then I want The Quillstone Chief on the back of it with my information.

I would like to see a light colored background as well as a dark colored background

FRONT:
BRIGHTVALE MEDIA LOGO
248 N. Larkmoor
3rd Floor
San Diego CA 92173
www.BrightvaleMedia.com

Advanced Website & App Development
Websites, Apps, Online Voucher Systems

Leading Edge Marketing Services
SMS, VB, SMM, SEM,

BACK:
QUILLSTONE CHIEF LOGO
Dorian Pelletta
The Quillstone Chief
Call Or Text: 619-555-0148
Dorian@QuillstoneChief.example
www.QuillstoneChief.example

Target Market(s)

small business owners

Industry/Entity Type

Business Consultant

Contact Information for Business Card

FRONT:
BRIGHTVALE MEDIA LOGO
248 N. Larkmoor
3rd Floor
San Diego CA 92173
www.BrightvaleMedia.com

SMS, VB, SMM, SEM,

BACK:
QUILLSTONE CHIEF LOGO
Dorian Pelletta
The Quillstone Chief
Dorian@QuillstoneChief.example
www.QuillstoneChief.example

Requirements
Must have
• add this quote on it somewhere, anywhere,preferrably on back
• "The Fastest Way To Success Is To Take Action”
• — Dorian Pelletta, Quillstone Chief
Nice to have
• open
Should not have
• red

```html
<!DOCTYPE html>
<html lang="en">
<head>
<meta charset="utf-8">
<title>Brightvale Media — Business Card</title>
<link rel="stylesheet" href="https://fonts.googleapis.com/css2?family=Open+Sans:ital,wght@0,400;0,600;1,400&display=swap">
<style>
  :root {
    --backdrop: #3a3a3a;
    --card: #ffffff;
    --brand-blue: #1a6ea8;
    --ink: #555555;
    --ink-soft: #7a7a7a;
    --rule: #d6d6d6;
  }
  * { margin: 0; padding: 0; box-sizing: border-box; }
  html, body {
    width: 1105px; height: 1200px; overflow: hidden;
    background: var(--backdrop);
    font-family: "Open Sans", Arial, sans-serif;
  }
  .card {
    position: absolute; left: 196px; width: 720px;
    background: var(--card); overflow: hidden;
  }
  .card--front { top: 146px; height: 412px; }
  .card--back  { top: 602px; height: 410px; }

  .wordmark {
    position: absolute; color: var(--brand-blue);
    font-weight: 600; letter-spacing: 2px; white-space: nowrap;
  }
  .card--front .wordmark {
    left: 203px; top: 205px; transform: translate(-50%, -50%);
    font-size: 27px;
  }
  .card--back .wordmark {
    right: 366px; top: 207px; transform: translateY(-50%);
    font-size: 25px;
  }

  .details {
    position: absolute; left: 381px; top: 70px;
    color: var(--ink); font-size: 19px; line-height: 25.5px;
  }
  .details .web { color: var(--brand-blue); font-weight: 600; margin-top: 2px; }
  .details .group { margin-top: 7px; }
  .details .group--services { margin-top: 8px; }
  .dot { color: var(--brand-blue); }

  .divider {
    position: absolute; left: 376px; top: 123px;
    width: 1px; height: 166px; background: var(--rule);
  }
  .identity { position: absolute; left: 398px; top: 124px; }
  .identity .name {
    color: var(--brand-blue); font-weight: 600; font-size: 25px; line-height: 32px;
  }
  .identity .title { color: var(--ink); font-size: 19px; line-height: 26px; }
  .contacts { list-style: none; margin-top: 14px; }
  .contacts li {
    display: flex; align-items: center; gap: 9px; white-space: nowrap;
    color: var(--ink); font-size: 17px; line-height: 27.5px;
  }
  .contacts svg { width: 16px; height: 16px; fill: var(--brand-blue); flex: none; }

  .quote {
    position: absolute; left: 0; right: 0; top: 338px;
    text-align: center; color: var(--ink-soft);
    font-size: 14px; line-height: 20px;
  }
  .quote q { font-style: italic; }
  .quote cite { font-style: normal; display: block; font-size: 12.5px; }
</style>
</head>
<body>

<section class="card card--front" aria-label="Card front">
  <div class="wordmark">BRIGHTVALE MEDIA</div>
  <div class="details">
    <p>248 N. Larkmoor</p>
    <p>3rd Floor</p>
    <p>San Diego CA 92173</p>
    <p class="web">BrightvaleMedia.com</p>
    <div class="group">
      <p>Advanced Website &amp;</p>
      <p>App Development</p>
      <p>Websites <span class="dot">•</span> Apps</p>
      <p>Online Voucher Systems</p>
    </div>
    <div class="group group--services">
      <p>Leading Edge Marketing Services</p>
      <p>SMS <span class="dot">•</span> VB <span class="dot">•</span> SMM <span class="dot">•</span> SEM</p>
    </div>
  </div>
</section>

<section class="card card--back" aria-label="Card back">
  <div class="wordmark">QUILLSTONE CHIEF</div>
  <div class="divider"></div>
  <div class="identity">
    <p class="name">Dorian Pelletta</p>
    <p class="title">The Quillstone Chief</p>
    <ul class="contacts">
      <li>
        <svg viewBox="0 0 24 24" aria-hidden="true"><path d="M6.6 10.8a15.1 15.1 0 0 0 6.6 6.6l2.2-2.2c.3-.3.7-.4 1-.2 1.1.4 2.3.6 3.6.6.6 0 1 .4 1 1V20c0 .6-.4 1-1 1C10.6 21 3 13.4 3 4c0-.6.4-1 1-1h3.5c.6 0 1 .4 1 1 0 1.3.2 2.5.6 3.6.1.3 0 .7-.2 1z"/></svg>
        619-555-0148
      </li>
      <li>
        <svg viewBox="0 0 24 24" aria-hidden="true"><path d="M2 5h20v1.6L12 13.5 2 6.6z"/><path d="M2 8.3l10 6.9 10-6.9V19H2z"/></svg>
        Dorian@QuillstoneChief.example
      </li>
      <li>
        <svg viewBox="0 0 24 24" aria-hidden="true"><circle cx="12" cy="12" r="10"/><path d="M2 12h20M12 2c3 3 3 17 0 20M12 2c-3 3-3 17 0 20" stroke="#fff" stroke-width="1.4" fill="none"/></svg>
        www.QuillstoneChief.example
      </li>
    </ul>
  </div>
  <blockquote class="quote">
    <q>The Fastest Way To Success Is To Take Action</q>
    <cite>— Dorian Pelletta, Quillstone Chief</cite>
  </blockquote>
</section>

</body>
</html>
```